Young, dynamic furniture company needs a new business card design

We require a new business card design for our modern furniture company which supplies furniture and appliances to the property and development market.
Oakridge Interiors has become one of the leading furniture & appliance suppliers to the property market withing London. With over 10 years experience, we have increased our business to supply not only private landlords and managing agents, but also property developers, housing associations and local councils.
We offer not only a complete range of furniture which includes beds, wardrobes, dining sets and sofas, but also a high quality, full delivery and assembly service to help you with all our furnishing needs.

Target Market(s)

Private landlords, estate agents, letting agents, property management companies

Industry/Entity Type

Business

Contact Information for Business Card

Name,
Title,
Address,
Mobile,
Telephone,
Fax, Website, email address

Font styles to use
Sans Serif

Colors
3176b5
0555a3
85abd2
cfdeed

Requirements
Must have
• All the above information for each of our staff, along with our logo

```html
<!DOCTYPE html>
<html lang="en">
<head>
<meta charset="utf-8">
<title>Oakridge Interiors – Business Card</title>
<link href="https://fonts.googleapis.com/css2?family=Arimo:wght@400;700&display=swap" rel="stylesheet">
<style>
  :root {
    --bg: #e6e8ec;
    --navy: #0a3f9a;
    --navy-deep: #0555a3;
    --navy-tab: #1d3f8f;
    --bright: #3176b5;
    --bright-hi: #2a86d8;
    --charcoal: #1c1c1e;
    --charcoal-2: #2a2a2d;
    --ink: #1b1b1d;
    --paper: #ffffff;
    --pale: #cfdeed;
  }
  * { box-sizing: border-box; margin: 0; padding: 0; }
  html, body { width: 1200px; height: 950px; overflow: hidden; }
  body {
    background: var(--bg);
    font-family: "Arimo", Arial, sans-serif;
    position: relative;
  }
  .card {
    position: absolute;
    left: 250px;
    width: 700px;
    height: 400px;
    overflow: hidden;
    box-shadow: 0 6px 18px rgba(0,0,0,.18);
  }
  /* Reverse side */
  .card--reverse {
    top: 40px;
    background: linear-gradient(160deg, var(--navy) 0%, var(--navy-tab) 60%, var(--navy-deep) 100%);
    color: var(--paper);
    text-align: center;
  }
  .brand {
    display: flex;
    align-items: center;
    gap: 12px;
  }
  .brand__mark { width: 26px; height: 26px; flex: none; }
  .brand__name {
    font-weight: 700;
    font-size: 30px;
    letter-spacing: .5px;
    text-transform: uppercase;
  }
  .brand__tagline {
    font-size: 11px;
    letter-spacing: 1.2px;
    text-transform: uppercase;
  }
  .card--reverse .brand { justify-content: center; margin-top: 120px; }
  .card--reverse .brand__mark { background: var(--paper); }
  .card--reverse .brand__tagline { margin-top: 6px; }
  .card__blurb {
    margin-top: 40px;
    font-size: 17px;
    line-height: 1.4;
  }

  /* Front side */
  .card--front { top: 510px; background: var(--paper); }
  .card__shapes { position: absolute; inset: 0; }
  .card--front .brand-block {
    position: absolute;
    right: 40px;
    top: 56px;
    text-align: right;
    color: var(--ink);
  }
  .card--front .brand { justify-content: flex-end; }
  .card--front .brand__mark { background: var(--bright); }
  .card--front .brand__name { font-size: 28px; font-weight: 400; }
  .card--front .brand__tagline { margin-top: 4px; font-size: 10px; }
  .person {
    position: absolute;
    left: 28px;
    top: 240px;
    color: var(--paper);
  }
  .person__name { font-weight: 700; font-size: 24px; letter-spacing: .5px; }
  .person__title { font-size: 15px; margin-top: 4px; letter-spacing: .5px; }
  .contacts {
    position: absolute;
    left: 28px;
    top: 322px;
    list-style: none;
    color: var(--paper);
    font-size: 15px;
  }
  .contacts li {
    display: flex;
    align-items: center;
    gap: 14px;
    height: 18.5px;
  }
  .contacts svg { width: 15px; height: 15px; fill: var(--paper); flex: none; }
  .address {
    position: absolute;
    right: 30px;
    top: 238px;
    text-align: right;
    color: var(--paper);
    font-size: 16px;
    line-height: 1.45;
    letter-spacing: .4px;
  }
  .address__web { letter-spacing: 2.5px; }
</style>
</head>
<body>

  <section class="card card--reverse" aria-label="Business card, reverse side">
    <div class="brand">
      <span class="brand__mark"></span>
      <span class="brand__name">Oakridge Interiors</span>
    </div>
    <p class="brand__tagline">Trade Furniture Solutions</p>
    <p class="card__blurb">High quality, full delivery &amp; assembly<br>service to help you with all our furnishing needs.</p>
  </section>

  <section class="card card--front" aria-label="Business card, front side">
    <svg class="card__shapes" viewBox="0 0 700 400" width="700" height="400" aria-hidden="true">
      <defs>
        <linearGradient id="charcoalFill" x1="0" y1="0" x2="1" y2="1">
          <stop offset="0" stop-color="#2a2a2d"/>
          <stop offset="1" stop-color="#151517"/>
        </linearGradient>
      </defs>
      <polygon points="330,242 700,128 700,155 420,250 340,250" fill="var(--bright-hi)"/>
      <polygon points="0,250 420,250 700,155 700,400 0,400" fill="url(#charcoalFill)"/>
      <polygon points="0,215 250,215 340,245 340,310 0,310" fill="var(--navy-tab)"/>
    </svg>

    <div class="brand-block">
      <div class="brand">
        <span class="brand__mark"></span>
        <span class="brand__name">OAKRIDGE INTERIORS</span>
      </div>
      <p class="brand__tagline">Trade Furniture Solutions</p>
    </div>

    <div class="person">
      <p class="person__name">MARA LINDQVIST</p>
      <p class="person__title">PRESIDENT</p>
    </div>

    <ul class="contacts">
      <li>
        <svg viewBox="0 0 16 16" aria-label="Telephone"><path d="M2 5c0-2 2-3 6-3s6 1 6 3v1h-3V4.5C10 4 6 4 5 4.5V6H2zM4 7h8l2 7H2z"/></svg>
        512 7390 4418
      </li>
      <li>
        <svg viewBox="0 0 16 16" aria-label="Mobile"><path d="M4 1h8v14H4zM5.5 3v9h5V3z"/></svg>
        847 2615 9302
      </li>
      <li>
        <svg viewBox="0 0 16 16" aria-label="Fax"><path d="M4 1h8v4H4zM1 6h14v6h-3v3H4v-3H1zM5.5 10v3.5h5V10z"/></svg>
        829 5041 7763
      </li>
      <li>
        <svg viewBox="0 0 16 16" aria-label="Email"><path d="M1 3h14v10H1zM2.5 4.5 8 9l5.5-4.5z"/></svg>
        mara@oakridge.co
      </li>
    </ul>

    <address class="address" style="font-style:normal">
      2170 Alder Crescent<br>
      Brookvale, NY 11420<br>
      <span class="address__web">www.oakridge.co</span>
    </address>
  </section>

</body>
</html>
```